Kelvaro.ch is looking for business card letterhead and envelope C5 with WOW effect

We need a strong business card for our company Kelvaro.ch, logo is available. You want a black or dark background on which the logo Stark r% 26 # 252; appears. Letterhead and envelope in C5 format should be in a similar design, but does not have to be We need a strong business card for our company Kelvaro.ch, logo is available. A black or dark background is desired, on which the logo Stark comes across. The letterhead and the envelope in C5 format should have a similar design.

Target Market(s)

Private customers as well as entrepreneurs

Contact Information for Business Card

E-mail: info@kelvaro-example.ch
Web.www.Kelvaro-example.ch
Tel: +41 ( 0 ) 79 482 6037
Adresse:
Lindenweg 14
9406 Tarnbach

Hier kann man Icons verwenden für Email,Tel und Adressse

Font styles to use
Other font styles liked:
• Dubai,bold

Colors

Designer to choose colors to be used in the design.

Requirements
Must have
• WOW effect
Nice to have
• R% 26 # 252; back business card with our service listings. - VEHICLE LABELING - SHOP WINDOW LABELING - STICKERS AND MUCH MORE ... in red color

```html
<!DOCTYPE html>
<html lang="en">
<head>
<meta charset="utf-8">
<title>Kelvaro.ch – Business Card</title>
<link rel="stylesheet" href="https://fonts.googleapis.com/css2?family=Open+Sans:wght@400;600;700;800&display=swap">
<style>
  :root {
    --stage: #1b1b1b;
    --card: #262626;
    --card-deep: #1f1f1f;
    --yellow: #fcc71e;
    --white: #f4f4f4;
    --silver: #a9a9a9;
    --red: #d8202a;
    --font: "Open Sans", Arial, sans-serif;
  }
  * { box-sizing: border-box; margin: 0; padding: 0; }
  html, body { width: 1200px; height: 900px; overflow: hidden; }
  body {
    background: var(--stage);
    font-family: var(--font);
    position: relative;
  }
  .card {
    position: absolute;
    left: 220px;
    width: 760px;
    height: 400px;
    background: linear-gradient(135deg, var(--card-deep) 0%, var(--card) 60%, #2c2c2c 100%);
    border-bottom: 7px solid var(--yellow);
    overflow: hidden;
  }
  .card--front { top: 36px; }
  .card--back { top: 466px; }

  /* front */
  .front-mark {
    position: absolute;
    left: 200px; top: 95px;
    width: 175px; height: 165px;
  }
  .front-name {
    position: absolute;
    left: 390px; top: 150px;
    font-size: 40px;
    font-weight: 800;
    color: var(--silver);
    letter-spacing: 1px;
  }
  .services {
    position: absolute;
    right: 90px; top: 225px;
    list-style: none;
    text-align: right;
  }
  .services li {
    color: var(--white);
    font-size: 15px;
    line-height: 21px;
    letter-spacing: 0.3px;
  }
  .services li::after {
    content: "";
    display: inline-block;
    width: 8px; height: 8px;
    margin-left: 14px;
    border: 2px solid var(--red);
    border-radius: 50%;
    vertical-align: middle;
  }

  /* back */
  .back-name {
    position: absolute;
    left: 48px; top: 30px;
    font-size: 38px;
    font-weight: 800;
    color: var(--white);
    letter-spacing: 1px;
  }
  .person {
    position: absolute;
    left: 60px; top: 128px;
  }
  .person__name {
    font-size: 27px;
    font-weight: 700;
    letter-spacing: 2.5px;
    color: var(--white);
    text-transform: uppercase;
  }
  .person__name .surname { color: var(--yellow); }
  .person__role {
    font-size: 15px;
    color: var(--white);
    letter-spacing: 1px;
  }
  .person__rule {
    width: 46px; height: 2px;
    background: var(--yellow);
    margin-top: 18px;
  }
  .contact {
    position: absolute;
    left: 60px; top: 238px;
    list-style: none;
  }
  .contact li {
    display: flex;
    align-items: center;
    gap: 10px;
    font-size: 17px;
    color: var(--white);
    line-height: 27px;
    letter-spacing: 0.5px;
  }
  .contact svg { width: 14px; height: 14px; flex: none; }
  .address {
    position: absolute;
    left: 60px; top: 330px;
    font-size: 18px;
    color: var(--white);
    letter-spacing: 1px;
  }
  .back-mark {
    position: absolute;
    left: 470px; top: 40px;
    width: 250px; height: 310px;
  }
</style>
</head>
<body>

<section class="card card--front">
  <svg class="front-mark" role="img" aria-label="Embossed company symbol" viewBox="0 0 175 165">
    <defs>
      <linearGradient id="emboss" x1="0" y1="0" x2="1" y2="1">
        <stop offset="0" stop-color="#2e2e2e"/>
        <stop offset="1" stop-color="#1c1c1c"/>
      </linearGradient>
    </defs>
    <rect width="175" height="165" rx="20" fill="url(#emboss)"/>
  </svg>
  <div class="front-name">Kelvaro.ch</div>
  <ul class="services">
    <li>VEHICLE LABELING</li>
    <li>SHOP WINDOW LABELING</li>
    <li>STICKERS AND MUCH MORE</li>
  </ul>
</section>

<section class="card card--back">
  <div class="back-name">Kelvaro.ch</div>
  <div class="person">
    <div class="person__name">Jonas <span class="surname">Brenner</span></div>
    <div class="person__role">Director</div>
    <div class="person__rule"></div>
  </div>
  <ul class="contact">
    <li>
      <svg viewBox="0 0 14 14" aria-hidden="true"><path d="M3 1h3l1 3-2 1.2a8 8 0 0 0 3.8 3.8L10 7l3 1v3a2 2 0 0 1-2 2A10 10 0 0 1 1 3a2 2 0 0 1 2-2z" fill="var(--yellow)"/></svg>
      +41 ( 0 ) 79 482 6037
    </li>
    <li>
      <svg viewBox="0 0 14 14" aria-hidden="true"><rect x="1" y="3" width="12" height="8" fill="none" stroke="var(--yellow)" stroke-width="1.4"/><path d="M1 3l6 5 6-5" fill="none" stroke="var(--yellow)" stroke-width="1.4"/></svg>
      info@kelvaro-example.ch
    </li>
    <li>
      <svg viewBox="0 0 14 14" aria-hidden="true"><circle cx="7" cy="7" r="6" fill="none" stroke="var(--yellow)" stroke-width="1.3"/><ellipse cx="7" cy="7" rx="2.6" ry="6" fill="none" stroke="var(--yellow)" stroke-width="1.1"/><path d="M1 7h12" stroke="var(--yellow)" stroke-width="1.1"/></svg>
      www.Kelvaro-example.ch
    </li>
  </ul>
  <div class="address">Lindenweg 14 9406 Tarnbach</div>
  <svg class="back-mark" role="img" aria-label="Large yellow company symbol" viewBox="0 0 250 310">
    <defs>
      <linearGradient id="mark" x1="0" y1="0" x2="0" y2="1">
        <stop offset="0" stop-color="#fcc71e"/>
        <stop offset="1" stop-color="#f4bd14"/>
      </linearGradient>
    </defs>
    <rect width="250" height="310" rx="24" fill="url(#mark)"/>
  </svg>
</section>

</body>
</html>
```